Business cards in digital learning for freelancer

Hello, I need a business cards in french. I work in the Digital learning industries as freeelancer; I'm an expert in digital learning. I work in France. My customer are in the health industry, pharmaceutical industry, and training organization. I've got a logo. I offer three services: consulting, Design, and Training. In the consulting, I offers coaching to choose your digital learning tools and the digital learning strategy. For the Design, I product differents level of elearning like rapid-learning, elearning, micro-learning, video-learning. And for the training service, I've create training about pedagogy, digital learning management project, Digital learning design.
I join my Logo create in this platform. My universe is gamified. I like the life, and I'm very social. I want a card like I'm I. I love Art (painting), Europeen comics. I use in my visual support "permanent maker" font and caracters. I would like cards: elegant, modern, Top class. If you need any information, you can ask me.
thanks for ideas

Target Market(s)

in health industries and training organization for Training manager, instructor, human resources director

Contact Information for Business Card

Phone number : 06 71 38 95 14 , mail: bastiengolmier@quelmoto.fr, web: bastiengolmier.fr , Carrivo

Font styles to use
Sans Serif

Requirements
Must have
• Use my logo and write my 3 services (consulting, training, design)

```html
<!DOCTYPE html>
<html lang="fr">
<head>
<meta charset="utf-8">
<title>Bastien Golmier – Cartes de visite</title>
<link rel="stylesheet" href="https://fonts.googleapis.com/css2?family=Montserrat:wght@500;600;700&family=Roboto:wght@400;700&family=Permanent+Marker&display=swap">
<style>
  :root {
    --bg: #2a2a2a;
    --card: #ffffff;
    --orange: #f07324;
    --grey: #7a7a7a;
    --grey-dark: #5f5f5f;
    --ghost: #ececec;
    --text-light: #ffffff;
  }
  * { box-sizing: border-box; margin: 0; padding: 0; }
  html, body { width: 1200px; height: 900px; overflow: hidden; }
  body {
    background: var(--bg);
    font-family: "Roboto", sans-serif;
    position: relative;
  }
  .card {
    position: absolute;
    left: 260px;
    width: 680px;
    height: 388px;
    border-radius: 26px;
    background: var(--card);
    overflow: hidden;
  }
  .card--front { top: 42px; }
  .card--back { top: 470px; }

  /* Front */
  .ghost-brand {
    position: absolute;
    right: -20px;
    top: 10px;
    font-family: "Montserrat", sans-serif;
    font-weight: 700;
    font-size: 120px;
    color: var(--ghost);
    line-height: 1;
    letter-spacing: -2px;
  }
  .brand {
    position: absolute;
    display: flex;
    align-items: center;
    gap: 12px;
    font-family: "Montserrat", sans-serif;
    font-weight: 700;
    color: var(--orange);
  }
  .brand__dot {
    width: 22px; height: 22px;
    border-radius: 50%;
    background: var(--grey);
    flex: none;
  }
  .card--front .brand { left: 215px; top: 135px; font-size: 46px; }
  .services {
    position: absolute;
    left: 0; right: 0;
    top: 262px;
    text-align: center;
    font-family: "Permanent Marker", cursive;
    font-size: 26px;
    letter-spacing: 2px;
    color: var(--grey-dark);
  }
  .services__sep {
    display: inline-block;
    width: 11px; height: 11px;
    border-radius: 50%;
    background: var(--orange);
    margin: 0 22px;
    vertical-align: middle;
  }

  /* Back */
  .back-shapes { position: absolute; inset: 0; }
  .card--back .brand { left: 52px; top: 290px; font-size: 38px; }
  .contact {
    position: absolute;
    left: 360px;
    top: 36px;
    color: var(--text-light);
  }
  .contact__name {
    font-family: "Montserrat", sans-serif;
    font-weight: 700;
    font-size: 28px;
    letter-spacing: 0.5px;
  }
  .contact__role {
    font-family: "Montserrat", sans-serif;
    font-weight: 600;
    font-size: 13px;
    margin-top: 2px;
    margin-bottom: 16px;
  }
  .contact__list { list-style: none; }
  .contact__item {
    display: flex;
    align-items: center;
    gap: 10px;
    font-size: 16px;
    line-height: 1.55;
  }
  .contact__item--phone { font-weight: 700; font-size: 21px; }
  .contact__icon { width: 18px; height: 18px; flex: none; }
  .contact__square {
    width: 14px; height: 14px;
    background: var(--text-light);
    margin: 0 2px;
    flex: none;
  }
</style>
</head>
<body>

<section class="card card--front">
  <div class="ghost-brand" aria-hidden="true">Golmier</div>
  <div class="brand"><span class="brand__dot"></span>Golmier</div>
  <p class="services">CONSULTING<span class="services__sep"></span>TRAINING<span class="services__sep"></span>DESIGN</p>
</section>

<section class="card card--back">
  <svg class="back-shapes" viewBox="0 0 680 388" width="680" height="388" aria-hidden="true">
    <path fill="var(--orange)" d="M0 0 H680 V340 L610 315 C540 250 440 150 340 150 C250 150 220 250 140 265 C80 276 30 262 0 250 Z"/>
    <path fill="var(--grey)" stroke="#ffffff" stroke-width="3"
      d="M680 0 H370 C315 0 290 45 298 88 C282 130 312 175 358 168 C338 215 372 262 420 255 C442 302 512 312 542 276 C572 302 632 292 642 250 C660 256 676 244 680 232 Z"/>
    <circle cx="292" cy="250" r="21" fill="var(--grey)" stroke="#ffffff" stroke-width="3"/>
  </svg>

  <div class="brand"><span class="brand__dot"></span>Golmier</div>

  <div class="contact">
    <h1 class="contact__name">Bastien GOLMIER</h1>
    <p class="contact__role">Digital Learning Consultant</p>
    <ul class="contact__list">
      <li class="contact__item contact__item--phone">
        <svg class="contact__icon" viewBox="0 0 24 24"><path fill="#fff" d="M6.6 10.8a15 15 0 0 0 6.6 6.6l2.2-2.2c.3-.3.7-.4 1-.2 1.1.4 2.3.6 3.6.6.6 0 1 .4 1 1V20c0 .6-.4 1-1 1A17 17 0 0 1 3 4c0-.6.4-1 1-1h3.5c.6 0 1 .4 1 1 0 1.3.2 2.5.6 3.6.1.3 0 .7-.2 1z"/></svg>
        06 71 38 95 14
      </li>
      <li class="contact__item">
        <svg class="contact__icon" viewBox="0 0 24 24"><rect x="2" y="5" width="20" height="14" rx="1" fill="#fff"/><path d="M3 6l9 7 9-7" fill="none" stroke="var(--grey)" stroke-width="1.8"/></svg>
        bastiengolmier@quelmoto.fr
      </li>
      <li class="contact__item">
        <svg class="contact__icon" viewBox="0 0 24 24" fill="none" stroke="#fff" stroke-width="1.6"><circle cx="12" cy="12" r="9"/><ellipse cx="12" cy="12" rx="4" ry="9"/><path d="M3 12h18M5 7h14M5 17h14"/></svg>
        bastiengolmier.fr
      </li>
      <li class="contact__item"><span class="contact__square"></span>Carrivo</li>
    </ul>
  </div>
</section>

</body>
</html>
```